Brightway Haus Inc. Business Card Design

Brightway Haus Inc. is in search of a great clean design for our business cards!

Looking to incorporate our full logo and watermark on side one (however, I am open to having the text and watermark separated within the design.)

On side two, I am looking to have contact information (Name, Position, Phone #, Email, Website (www.thebrightwayhaus.ca). Can have the logo and/or watermark as part of the design if applicable.

Please add tagline "Where Shine Counts" on either side 1 or 2. This tagline can be in a sans serif, serif or cursive font as long as it compliments overall design. Capitalization can be title or sentence case depending on how it fits within the design.

Get creative!! Looking for a clean, crisp, premium design! Looking for a glossy card finish with spot UV features when printed. Cards will also be printed with rounded corners. Standard dimensions (3.5 x 2).

Target Market(s)

B2B - primary clients are business owners or property management corporations. (residential jobs are few and far between)

Industry/Entity Type

Business

Contact Information for Business Card

- clean, crisp design
- double sided
- spot UV accents and glossy finish upon printing
- standard business card size (3.5 x 2) with rounded corners
- please see project description for requirements per side

Font styles to use
Sans Serif

Requirements
Must have
• - adequate bleeds with print ready files
• - cohesive design elements between side 1 & 2
• - spot UV elements (can be on both sides or just one, use your discretion)
• - colour pallet should match the logo file provided
• - incorporate tagline "where shine counts" (this tagline can be in a serif or sans serif font as long as it is complimentary to the overall design.
Nice to have
• - Premium elements with a clean design
Should not have
• - Please omit cartoon or whimsical like designs, think premium.
• - Colours should not stray from the pallet of the provided logo.

```html
<!DOCTYPE html>
<html lang="en">
<head>
<meta charset="utf-8">
<title>Brightway Haus Inc. Business Cards</title>
<link rel="stylesheet" href="https://fonts.googleapis.com/css2?family=Open+Sans:wght@700;800&family=Roboto:wght@400;500&display=swap">
<style>
  :root {
    --stage: #2b2b2c;
    --card-dark: #1e2022;
    --card-light: #f4f4f4;
    --teal: #14b5b8;
    --navy: #1f2a5a;
    --ink: #4a4a4a;
    --white: #ffffff;
  }
  html, body {
    margin: 0;
    width: 1200px;
    height: 960px;
    overflow: hidden;
    background: var(--stage);
  }
  .canvas {
    position: relative;
    width: 1200px;
    height: 960px;
  }
  .card {
    position: absolute;
    width: 600px;
    height: 342px;
    border-radius: 22px;
    overflow: hidden;
    box-sizing: border-box;
  }
  .card--front {
    left: 320px;
    top: 108px;
    background: var(--card-dark);
  }
  .card--back {
    left: 320px;
    top: 493px;
    background: var(--card-light);
  }
  .brand-name {
    font-family: "Open Sans", sans-serif;
    font-weight: 800;
    color: var(--teal);
    white-space: nowrap;
    letter-spacing: -1px;
    margin: 0;
  }
  .card--front .brand-name {
    position: absolute;
    left: 0;
    right: 0;
    top: 126px;
    text-align: center;
    font-size: 50px;
    line-height: 1;
  }
  .tagline {
    position: absolute;
    left: 0;
    right: 0;
    top: 194px;
    text-align: center;
    font-family: "Roboto", sans-serif;
    font-size: 15px;
    letter-spacing: 8.5px;
    color: var(--white);
    margin: 0;
  }
  .card--back .brand-name {
    position: absolute;
    right: 36px;
    top: 38px;
    font-size: 36px;
    line-height: 1;
  }
  .contact {
    position: absolute;
    left: 29px;
    top: 118px;
    font-family: "Roboto", sans-serif;
  }
  .contact__marker {
    position: absolute;
    left: -29px;
    top: 4px;
    width: 14px;
    height: 14px;
    border-radius: 50%;
    background: var(--teal);
  }
  .contact__name {
    margin: 0;
    font-size: 20px;
    font-weight: 500;
    color: var(--teal);
    line-height: 24px;
  }
  .contact__role {
    margin: 0;
    font-size: 15px;
    font-weight: 500;
    color: var(--navy);
    line-height: 20px;
  }
  .contact__address {
    margin: 12px 0 0;
    font-size: 14.5px;
    color: var(--ink);
    line-height: 18px;
    font-style: normal;
  }
  .contact__list {
    list-style: none;
    margin: 12px 0 0;
    padding: 0;
  }
  .contact__list li {
    display: flex;
    align-items: center;
    gap: 8px;
    font-size: 14.5px;
    color: var(--ink);
    line-height: 19px;
  }
  .contact__list svg {
    width: 14px;
    height: 14px;
    fill: var(--teal);
    flex: none;
  }
</style>
</head>
<body>
<main class="canvas">
  <section class="card card--front" aria-label="Card front">
    <h1 class="brand-name">BRIGHTWAY HAUS INC.</h1>
    <p class="tagline">Where Shine Counts</p>
  </section>

  <section class="card card--back" aria-label="Card back">
    <p class="brand-name">BRIGHTWAY HAUS INC.</p>
    <div class="contact">
      <span class="contact__marker"></span>
      <h2 class="contact__name">MARTA LINDQVIST</h2>
      <p class="contact__role">CEO/FOUNDER</p>
      <address class="contact__address">214 Alder Crescent<br>Halifax, Nova Scotia 30418</address>
      <ul class="contact__list">
        <li><svg viewBox="0 0 16 16" aria-hidden="true"><path d="M3.5 1.5l2.5 0 1 3.5-1.8 1.2a9 9 0 0 0 4.6 4.6L11 9l3.5 1v2.5c0 1-1 2-2 2A11 11 0 0 1 1.5 3.5c0-1 1-2 2-2z"/></svg>902 555 0147</li>
        <li><svg viewBox="0 0 16 16" aria-hidden="true"><path d="M4.5 0.5h7a1 1 0 0 1 1 1v13a1 1 0 0 1-1 1h-7a1 1 0 0 1-1-1v-13a1 1 0 0 1 1-1zM5 2.5v9.5h6V2.5zM8 12.8a.9.9 0 1 0 0 1.8.9.9 0 0 0 0-1.8z"/></svg>902 555 0193</li>
        <li><svg viewBox="0 0 16 16" aria-hidden="true"><path d="M4 1h8v4H4zM1.5 6h13a1 1 0 0 1 1 1v5h-3v3h-9v-3h-3V7a1 1 0 0 1 1-1zM5 11v2.5h6V11z"/></svg>902 555 0162</li>
        <li><svg viewBox="0 0 16 16" aria-hidden="true"><path d="M1 3h14v1L8 8.5 1 4zM1 5.5l7 4.5 7-4.5V13H1z"/></svg>marta@thebrightwayhaus.ca</li>
        <li><svg viewBox="0 0 16 16" aria-hidden="true"><path d="M8 1a7 7 0 1 0 0 14A7 7 0 0 0 8 1zm-1 2.2c-.4 1-.2 2 .8 2.3 1 .4 1.2 1.3.6 2-.6.7-1.9.4-2.4 1.4-.4.8.2 1.7-.2 2.6-.3.7-1.3.8-1.9.3A5.5 5.5 0 0 1 7 3.2zm3 1c1.9.9 3.2 2.8 3.2 5 0 .5 0 1-.2 1.4-.6-.6-1.6-.4-2-1.3-.5-1 .6-1.8.1-2.7-.4-.8-1.4-.8-1.1-2.4z"/></svg>www.thebrightwayhaus.ca</li>
      </ul>
    </div>
  </section>
</main>
</body>
</html>
```